Professional, modern and unique business card. We are looking to present a new look to our business cards however we don't want to divert too far away from original template. We want social media links and our 3 office addresses on the backside of the business cards. Please see attached business card templates for ideas.
Crestline Homes Color Code:
R: 7
G:63
B:86

Target Market(s)

Real Estate

Industry/Entity Type

Real Estate

Contact Information for Business Card

Follow the attached templates. In need of a more modern and unique touch but don't want to divert from the original theme or color.
Crestline Homes Color Code:
R: 7
G:63
B:86

Font styles to use
Serif

Requirements
Must have
• Crestline Homes logo, Crestline homes colors, social media links, 3 office addresses,
Nice to have
• information about Crestline Homes and QR codes. You can check out www.mycrestlinehomes.example

```html
<!DOCTYPE html>
<html lang="en">
<head>
<meta charset="utf-8">
<title>Crestline Homes — Business Card</title>
<link href="https://fonts.googleapis.com/css2?family=Libre+Baskerville:wght@400;700&family=Work+Sans:wght@400;500&display=swap" rel="stylesheet">
<style>
  :root {
    --page: #3a3330;
    --card-dark: #1c1d1f;
    --card-light: #ffffff;
    --brand-blue: rgb(7, 63, 86);
    --accent: #1a7cc1;
    --accent-soft: #a9d6ee;
    --ink: #2a2a2a;
    --ink-white: #f2f2f2;
  }
  * { margin: 0; padding: 0; box-sizing: border-box; }
  html, body {
    width: 1200px; height: 715px; overflow: hidden;
    background: var(--page);
    font-family: "Work Sans", Arial, sans-serif;
  }
  .stage { position: relative; width: 1200px; height: 715px; }
  .card {
    position: absolute; top: 209px;
    width: 520px; height: 297px;
    overflow: hidden;
    box-shadow: 0 12px 30px rgba(0,0,0,.45);
  }
  .brand {
    position: absolute; left: 0; right: 0; text-align: center;
    font-family: "Libre Baskerville", Georgia, serif;
    font-weight: 700; letter-spacing: .5px; white-space: nowrap;
  }

  /* Back side */
  .card-back {
    left: 50px; background: var(--card-dark);
    border-bottom: 6px solid var(--brand-blue);
  }
  .card-back .brand { top: 78px; font-size: 36px; color: var(--accent-soft); }
  .social {
    position: absolute; left: 0; right: 0; top: 140px;
    display: flex; justify-content: center; align-items: center; gap: 8px;
    list-style: none; color: var(--ink-white); font-size: 12.5px;
  }
  .social .dot {
    width: 14px; height: 14px; border-radius: 50%; background: var(--accent-soft);
  }
  .social .handle { margin-left: 4px; }
  .addresses {
    position: absolute; left: 28px; right: 28px; bottom: 30px;
    display: flex; justify-content: space-between;
    color: var(--ink-white); font-size: 12.5px; line-height: 1.45;
  }
  .address { padding: 0 14px; }
  .address + .address { border-left: 1px solid var(--ink-white); }
  .address:first-child { padding-left: 0; }

  /* Front side */
  .card-front { left: 630px; background: var(--card-light); }
  .card-front .brand {
    top: 40px; left: 40px; right: auto; text-align: left;
    font-size: 30px; color: var(--ink);
  }
  .rule-top {
    position: absolute; left: 40px; top: 104px; width: 440px;
    height: 1.5px; background: var(--brand-blue);
  }
  .contacts {
    position: absolute; left: 40px; top: 126px;
    list-style: none; font-size: 13px; color: var(--ink); line-height: 1.6;
  }
  .contacts li { display: flex; align-items: center; gap: 8px; }
  .contacts svg { width: 10px; height: 10px; fill: var(--brand-blue); flex: none; }
  .person {
    position: absolute; right: 40px; top: 188px; text-align: right;
    border-bottom: 1.5px solid var(--brand-blue); padding-bottom: 5px;
  }
  .person-name {
    font-family: "Libre Baskerville", Georgia, serif;
    font-size: 19px; font-weight: 700; color: var(--brand-blue); letter-spacing: .5px;
  }
  .person-title { font-size: 12.5px; color: var(--ink); margin-top: 2px; }
  .band { position: absolute; left: 0; bottom: 0; width: 520px; height: 56px; }
</style>
</head>
<body>
<main class="stage">
  <section class="card card-back">
    <div class="brand">Crestline Homes</div>
    <ul class="social" aria-label="Social media">
      <li class="dot"></li>
      <li class="dot"></li>
      <li class="dot"></li>
      <li class="handle">@crestlinehomes</li>
    </ul>
    <div class="addresses">
      <p class="address">412 Harbor View Rd<br>Lakeport, NY 10990</p>
      <p class="address">78 Maple Crest Ave<br>Fairhill, NY 10921</p>
      <p class="address">950 Willow Park Dr<br>Eastbrook, NY 10934</p>
    </div>
  </section>

  <section class="card card-front">
    <div class="brand">Crestline Homes</div>
    <div class="rule-top"></div>
    <ul class="contacts">
      <li><svg viewBox="0 0 10 10"><path d="M2 0h2l1 3-1.5 1a6 6 0 0 0 2.5 2.5L7 5l3 1v2a2 2 0 0 1-2 2A8 8 0 0 1 0 2a2 2 0 0 1 2-2z"/></svg>555-014-2231</li>
      <li><svg viewBox="0 0 10 10"><path d="M2.5 0h5a1 1 0 0 1 1 1v8a1 1 0 0 1-1 1h-5a1 1 0 0 1-1-1V1a1 1 0 0 1 1-1zm.5 1.5v6h4v-6z"/></svg>555-014-7786</li>
      <li><svg viewBox="0 0 10 10"><path d="M0 2h10v6H0zM1 3v.3l4 2.5 4-2.5V3z"/></svg>info@mycrestlinehomes.example</li>
      <li><svg viewBox="0 0 10 10"><circle cx="5" cy="5" r="5"/></svg>www.mycrestlinehomes.example</li>
    </ul>
    <div class="person">
      <div class="person-name">DANIEL HARPER</div>
      <div class="person-title">Associate Real Estate Broker</div>
    </div>
    <svg class="band" viewBox="0 0 520 56" preserveAspectRatio="none" aria-hidden="true">
      <polygon points="0,20 0,56 120,56" fill="var(--card-dark)"/>
      <polygon points="175,0 520,0 520,56 120,56" fill="var(--brand-blue)"/>
    </svg>
  </section>
</main>
</body>
</html>
```